Its time for a new website

We are at a point now where we are in desperate need of a new website. It was last updated 2006 but still looks like its 1995. We are looking for something eye catching to our clients but easy to navigate and add/remove photos of jobs/trucks and information. Our key business is the manufacture of fire appliances and resale of parts and equipment.

www.kestrelrigs.com.au

Coding

Coded - Design and coding required

Number of Pages Required

5+ page

Requirements
Must have
• Logo

```html
<!DOCTYPE html>
<html lang="en">
<head>
<meta charset="utf-8">
<title>Kestrel Rigs — Custom Firefighting Equipment</title>
<link rel="stylesheet" href="https://fonts.googleapis.com/css2?family=Roboto+Condensed:wght@300;400;700&family=Open+Sans:wght@400;600&family=Raleway:wght@400;500&family=Roboto:wght@300;400&display=swap">
<style>
:root{
  --red:#e00b0b;
  --red-dark:#c50808;
  --ink:#222222;
  --body:#555555;
  --panel:#f2f2f2;
  --dark:#2a2a2a;
  --logo-bg:#231c1a;
  --blue:#1a7ac4;
  --link-blue:#1d4f8a;
  --white:#ffffff;
}
*{margin:0;padding:0;box-sizing:border-box}
html,body{width:1200px;height:2166px;overflow:hidden;background:var(--white)}
body{position:relative;font-family:"Open Sans",sans-serif;color:var(--body)}
.abs{position:absolute}

/* header */
.site-header{left:0;top:0;width:1200px;height:104px;background:var(--red)}
.brand{left:92px;top:0;width:207px;height:156px;background:var(--logo-bg);box-shadow:0 2px 6px rgba(0,0,0,.4);display:flex;flex-direction:column;align-items:center;justify-content:center;gap:10px;z-index:5}
.brand-mark{width:26px;height:26px;border-radius:50%;background:var(--red)}
.brand-name{font-family:"Roboto Condensed",sans-serif;font-weight:700;font-size:26px;color:var(--white)}
.main-nav{right:56px;top:46px;display:flex;gap:30px;font-family:"Roboto Condensed",sans-serif;font-size:13px;color:var(--white);text-transform:uppercase;letter-spacing:-.2px}

/* hero */
.hero{left:0;top:104px;width:1200px;height:625px;background:linear-gradient(180deg,#a9cfe9 0%,#dbe8ef 55%,#b9bcbe 70%,#9ea2a5 100%)}
.hero-truck{left:560px;top:30px;width:640px;height:590px;background:linear-gradient(160deg,#d9d9d9 0%,#c91d1d 45%,#8d1212 80%,#3b3b3b 100%);border-radius:6px 0 0 0;opacity:.9}
.hero-title{left:97px;top:335px;font-family:"Roboto Condensed",sans-serif;font-weight:700;font-size:52px;color:var(--ink);letter-spacing:-1px}
.hero-sub{left:97px;top:398px;font-family:"Roboto Condensed",sans-serif;font-size:33px;color:var(--ink)}
.hero-text{left:100px;top:455px;width:360px;font-size:13px;line-height:21px;color:#444}
.quote-btn{display:flex;height:44px;font-size:15px;color:var(--white);text-transform:uppercase}
.quote-btn .label{display:flex;align-items:center;padding:0 16px;border-radius:4px 0 0 4px}
.quote-btn .arrow{width:44px;background:#2c2c2c;display:flex;align-items:center;justify-content:center;border-radius:0 4px 4px 0}
.hero .quote-btn{left:97px;top:415px}
.red-btn .label{background:var(--red)}
.blue-btn .label{background:var(--blue)}
.slide-arrow{width:34px;height:34px;border-radius:50%;background:rgba(255,255,255,.55);display:flex;align-items:center;justify-content:center}

/* services */
.services{left:98px;top:682px;width:394px;height:450px;background:var(--white);box-shadow:0 0 4px rgba(0,0,0,.25);z-index:4}
.service{position:absolute;left:10px;width:374px;height:137px;background:var(--panel);padding:20px 18px}
.service h3{font-family:"Roboto Condensed",sans-serif;font-weight:300;font-size:26px;color:var(--ink);margin-bottom:8px}
.service p{font-size:11px;line-height:19px;width:215px}
.service svg{position:absolute;top:40px}
.service.featured{background:var(--red)}
.service.featured h3,.service.featured p{color:var(--white)}
.service.icon-left{padding-left:145px}

/* welcome */
.welcome{left:531px;top:780px;width:575px}
.welcome .kicker{font-family:"Roboto",sans-serif;font-weight:300;font-size:30px;color:var(--ink)}
.welcome h2{font-family:"Roboto",sans-serif;font-weight:400;font-size:40px;color:var(--red);margin-bottom:14px}
.welcome p{font-size:11.5px;line-height:20.8px;margin-bottom:20px}

/* promo band */
.promo{left:0;top:1089px;width:1200px;height:543px;background:linear-gradient(120deg,#3d4a3c 0%,#5c5a57 40%,#8e2b2b 62%,#5b5f63 100%)}
.promo-title{left:97px;top:1275px;font-family:"Roboto Condensed",sans-serif;font-weight:700;font-size:35px;color:var(--white)}
.promo-text{left:100px;top:1334px;width:440px;font-size:13px;line-height:22.5px;color:var(--white)}
.promo .quote-btn{left:97px;top:375px}

/* about */
.section-title{font-family:"Raleway",sans-serif;font-size:30px;color:var(--red);padding-bottom:14px;border-bottom:1px solid #e6e6e6}
.about{left:100px;top:1680px;width:673px}
.about-photo{left:100px;top:1760px;width:258px;height:224px;background:linear-gradient(180deg,#8fa4b4 0%,#c7b89a 55%,#a68b68 100%)}
.about-text{left:383px;top:1755px;width:392px;font-size:11px;line-height:20.5px}
.about-text p{margin-bottom:12px}
.read-more{left:383px;top:1972px;font-family:"Raleway",sans-serif;font-size:13px;color:var(--ink);display:flex;align-items:center;gap:10px}

.news{left:822px;top:1684px;width:283px}
.news h2{font-family:"Raleway",sans-serif;font-weight:500;font-size:26px;color:#333;padding-bottom:16px;border-bottom:1px solid #e6e6e6}
.news h2 span{color:var(--red)}
.news-item{padding:20px 0 22px;border-bottom:1px solid #e6e6e6}
.news-item:last-child{border:0}
.news-item h4{font-family:"Raleway",sans-serif;font-weight:500;font-size:14px;color:var(--link-blue);margin-bottom:10px}
.news-item time{display:flex;align-items:center;gap:6px;font-size:11.5px;margin-bottom:10px}
.news-item p{font-size:11.5px;line-height:20px}

/* footer */
.site-footer{left:0;top:2061px;width:1200px;height:105px;background:var(--dark);color:var(--white)}
.foot-col{top:32px}
.foot-col h5{font-family:"Raleway",sans-serif;font-weight:400;font-size:19px;margin-bottom:4px}
.foot-col p{font-size:11px}
.follow{left:888px;top:38px;display:flex;align-items:center;gap:6px}
.follow h5{font-family:"Raleway",sans-serif;font-weight:400;font-size:19px;margin-right:14px}
.social{width:24px;height:24px;background:var(--white);border-radius:3px}
.foot-tag{left:1142px;top:50px;font-size:10px}
</style>
</head>
<body>

<header class="abs site-header">
  <nav class="abs main-nav">
    <span>Home</span><span>About Us</span><span>Pumpers</span><span>GPA/Rescue</span><span>Light Tankers</span><span>Trailers</span><span>Slip-on Units</span><span>Contact Us</span>
  </nav>
</header>
<div class="abs brand"><span class="brand-mark"></span><span class="brand-name">Kestrel Rigs</span></div>

<section class="abs hero">
  <div class="abs hero-truck" role="img" aria-label="Red aerial ladder fire truck parked on a wide paved road"></div>
  <div class="abs slide-arrow" style="left:33px;top:325px"><svg width="12" height="12" viewBox="0 0 12 12"><path d="M8 1 3 6l5 5" fill="none" stroke="#666" stroke-width="2"/></svg></div>
  <div class="abs slide-arrow" style="left:1129px;top:325px"><svg width="12" height="12" viewBox="0 0 12 12"><path d="M4 1l5 5-5 5" fill="none" stroke="#666" stroke-width="2"/></svg></div>
  <a class="abs quote-btn red-btn"><span class="label">Get a quote now!</span><span class="arrow"><svg width="14" height="14" viewBox="0 0 14 14"><path d="M1 7h10M7 2l5 5-5 5" fill="none" stroke="#fff" stroke-width="2.4"/></svg></span></a>
</section>
<h1 class="abs hero-title">KESTREL RIGS</h1>
<p class="abs hero-sub">Narrogin Western Australia</p>
<p class="abs hero-text">Kestrel Rigs are Western Australia's leading manufacturer of custom firefighting equipment</p>

<section class="abs services">
  <article class="service featured" style="top:10px">
    <h3>Pumpers</h3>
    <p>Lorem ipsum dolor sit amet, consectetur adipiscing elit, sed do eiusmod tempor incididunt ut labore et dolore</p>
    <svg style="right:24px" width="80" height="52" viewBox="0 0 80 52"><rect x="2" y="16" width="74" height="24" rx="2" fill="#fff"/><rect x="46" y="6" width="24" height="14" fill="#fff"/><rect x="50" y="10" width="8" height="6" fill="var(--red)"/><path d="M4 12h38M4 8h38" stroke="#fff" stroke-width="2"/><circle cx="18" cy="42" r="6" fill="#fff" stroke="var(--red)" stroke-width="3"/><circle cx="60" cy="42" r="6" fill="#fff" stroke="var(--red)" stroke-width="3"/></svg>
  </article>
  <article class="service icon-left" style="top:156px">
    <h3>GPA/Rescue</h3>
    <p>Lorem ipsum dolor sit amet, consectetur adipiscing elit, sed do eiusmod tempor incididunt ut labore et dolore</p>
    <svg style="left:24px" width="92" height="60" viewBox="0 0 92 60"><path d="M2 8h62l24 22v18H2z" fill="#222"/><rect x="66" y="14" width="12" height="12" fill="var(--panel)"/><path d="M30 18v18M21 27h18" stroke="var(--panel)" stroke-width="6"/><circle cx="20" cy="50" r="8" fill="#222" stroke="var(--panel)" stroke-width="3"/><circle cx="70" cy="50" r="8" fill="#222" stroke="var(--panel)" stroke-width="3"/></svg>
  </article>
  <article class="service" style="top:301px">
    <h3>Slip-on Units</h3>
    <p>Lorem ipsum dolor sit amet, consectetur adipiscing elit, sed do eiusmod tempor incididunt ut labore et dolore</p>
    <svg style="right:36px;top:38px" width="64" height="64" viewBox="0 0 64 64"><path d="M60 4 4 28l20 8 6 22 10-16 14 8z M24 36 60 4 30 58" fill="none" stroke="#222" stroke-width="4" stroke-linejoin="round"/></svg>
  </article>
</section>

<section class="abs welcome">
  <p class="kicker">WELCOME TO</p>
  <h2>Kestrel Rigs</h2>
  <p>Lorem ipsum dolor sit amet, consectetur adipiscing elit, sed do eiusmod tempor incididunt ut labore et dolore magna aliqua. Ut enim ad minim veniam, quis nostrud exercitation ullamco laboris nisi ut aliquip ex ea commodo consequat. Duis aute irure dolor in reprehenderit in voluptate velit esse cillum dolore eu fugiat nulla pariatur. Excepteur sint occaecat cupidatat non proident.</p>
  <p>Lorem ipsum dolor sit amet, consectetur adipiscing elit, sed do eiusmod tempor incididunt ut labore et dolore magna aliqua. Ut enim ad minim veniam, quis nostrud exercitation ullamco laboris nisi ut aliquip ex ea commodo consequat. Duis aute irure dolor in reprehenderit in voluptate</p>
</section>

<section class="abs promo" role="img" aria-label="Red and white rescue van with striped livery parked beside trees and an office building">
  <div class="abs slide-arrow" style="left:33px;top:255px;background:rgba(0,0,0,.35)"><svg width="12" height="12" viewBox="0 0 12 12"><path d="M8 1 3 6l5 5" fill="none" stroke="#fff" stroke-width="2"/></svg></div>
  <div class="abs slide-arrow" style="left:1129px;top:255px;background:rgba(0,0,0,.35)"><svg width="12" height="12" viewBox="0 0 12 12"><path d="M4 1l5 5-5 5" fill="none" stroke="#fff" stroke-width="2"/></svg></div>
  <a class="abs quote-btn blue-btn"><span class="label">Get a quote now!</span><span class="arrow"><svg width="14" height="14" viewBox="0 0 14 14"><path d="M1 7h10M7 2l5 5-5 5" fill="none" stroke="#fff" stroke-width="2.4"/></svg></span></a>
</section>
<h2 class="abs promo-title">NEW APPLIANCES for 2006</h2>
<p class="abs promo-text">Lorem ipsum dolor sit amet, consectetur adipiscing elit, sed do eiusmod tempor incididunt ut labore et dolore magna aliqua. Ut enim ad minim veniam, quis nostrud exercitation ullamco laboris nisi ut aliquip ex ea commodo consequat. Duis aute irure dolor in reprehenderit in voluptate velit esse cillum dolore eu fugiat nulla pariatur.</p>

<section class="abs about"><h2 class="section-title">Narrogin Western Australia</h2></section>
<div class="abs about-photo" role="img" aria-label="White light tanker utility truck with red stripes parked on red dirt among gum trees"></div>
<div class="abs about-text">
  <p>Lorem ipsum dolor sit amet, consectetur adipiscing elit, sed do eiusmod tempor incididunt ut labore et dolore magna aliqua. Ut enim ad minim veniam, quis nostrud exercitation Lorem ipsum dolor sit amet, consectetur adipiscing elit, sed do eiusmod tempor incididunt ut labore et dolore magna aliqua. Ut enim ad minim veniam,</p>
  <p>Lorem ipsum dolor sit amet, consectetur adipiscing elit, sed do eiusmod tempor incididunt ut labore et dolore magna aliqua. Ut enim ad minim veniam, quis nostrud exercitation Lorem ipsum dolor sit amet, consectetur adipiscing elit, sed do eiusmod tempor incididunt</p>
</div>
<a class="abs read-more">READ MORE <svg width="13" height="13" viewBox="0 0 13 13"><circle cx="6.5" cy="6.5" r="6.5" fill="#222"/><path d="M5 3.5l3 3-3 3" fill="none" stroke="#fff" stroke-width="1.8"/></svg></a>

<aside class="abs news">
  <h2>Latest <span>News</span></h2>
  <article class="news-item">
    <h4>Nemo Enim Ipsam Voluptatem</h4>
    <time><svg width="11" height="11" viewBox="0 0 11 11"><circle cx="5.5" cy="5.5" r="4.5" fill="none" stroke="#333" stroke-width="1.6"/><path d="M5.5 3v3h2" fill="none" stroke="#333" stroke-width="1.3"/></svg>19.00 pm - 21.00 pm</time>
    <p>Vivamus elementum semper nisi. Lorem ipsum dolor sit amet, sectetuer adipiscing elit.</p>
  </article>
  <article class="news-item">
    <h4>Nemo Enim Ipsam Voluptatem</h4>
    <time><svg width="11" height="11" viewBox="0 0 11 11"><circle cx="5.5" cy="5.5" r="4.5" fill="none" stroke="#333" stroke-width="1.6"/><path d="M5.5 3v3h2" fill="none" stroke="#333" stroke-width="1.3"/></svg>19.00 pm - 21.00 pm</time>
    <p>Vivamus elementum semper nisi. Lorem ipsum dolor sit amet, sectetuer adipiscing elit.</p>
  </article>
</aside>

<footer class="abs site-footer">
  <div class="abs foot-col" style="left:100px"><h5>COPYRIGHT</h5><p>(c) 2015 Kestrel Rigs. All rights reserved.</p></div>
  <div class="abs foot-col" style="left:459px"><h5>ADDRESS</h5><p>214 Station Rd, Kestrel Rigs, Narrogin WA 6312</p></div>
  <div class="abs follow"><h5>FOLLOW US</h5><span class="social"></span><span class="social"></span><span class="social"></span></div>
  <span class="abs foot-tag">c7</span>
</footer>

</body>
</html>
```